Research and Innovation programme/projects in WOOD based industries

1.Pramenova s.r.o. (offical registered brand name of our company)
-Managing technology development projects
-International cooperation and development European projects
Our company was founded in 2008 and started to work as a counsilary company operating in the section of european funds administrated by Czech republic. Nowadays we are specializing on projects in the sphere of science and research co-financed by EU.Since 6.6.2013 we are registered under European comission for a purpose of broad support of transnational projects.

Target Market(s)

We are primarily focused on european companies, which stand behind the latest research and innovation of sawing, planing, glulam and logging technologies based on wooden materials.

Coding

Coded - Design and coding required

Number of Pages Required

5+ page

Font styles to use
Serif

Colors
cadf82
abd037
9bcb3c
fee18a
ffcf3e
ffc214

Requirements
Must have
• The web will exist in three possible languages in czech, english and deutsch.
• First page : introduction of a company
• Second page : Area of expertise
• Third page: servicies our company provides
• Fourth page: Our partners
• Fifth page: Conditions of our servicies
• Sixth page: Succesful projects
• - we would also love if we had possibility to add videos about our successful projects
• Seventh: Our team
• We are serious company in the sphere of funds and counsilary servicies, that is why we would love to have web design as representative as possible
• Take on mind that that we are specializing on development management, try to apply that on your design
• In the section of contacts, we would love to have photos of our team,
• This is our current site: http://www.pramenova-example.eu/cz/partneri.html
• This is how our concurency sites are lookin. Take these designs as an slight inspiration.
• http://www.lumatrava-example.sk/en/
• https://www2.brenvick-example.com/global/en.html
Nice to have
• Visible logo on the front page for the visitor.
• As a inspiration we provided link for our current web design, but we dont want to copy the current style, just look at the logo and the pages that exists on current web.
• !!!!!!We also uploaded file, where we explain how our cooperation with partner works. Especially in the part 2. section of service. Take that as an ispiration too, or use that to understand, what our company do.
Should not have
• We are serious company in the sphere of funds and counsilary servicies, that is why we would love to have web design representative as possible

```html
<!DOCTYPE html>
<html lang="en">
<head>
<meta charset="utf-8">
<title>1. Pramenova SRO – Beratungsfirma</title>
<link href="https://fonts.googleapis.com/css2?family=Fira+Sans:wght@500;600;700&family=Lato:wght@400;700&display=swap" rel="stylesheet">
<style>
:root{
  --green:#0f8a3c;
  --green-dark:#0b7a34;
  --lime:#9bcb3c;
  --lime-light:#cadf82;
  --orange:#ffa400;
  --yellow:#ffc214;
  --yellow-light:#fee18a;
  --text:#555;
  --dark:#2f2f2f;
  --gray-bg:#f2f2f2;
}
*{margin:0;padding:0;box-sizing:border-box}
html,body{width:1200px;height:4827px;overflow:hidden}
body{position:relative;font-family:"Lato",sans-serif;color:var(--text);background:#fff}
.abs{position:absolute}
h1,h2,h3{font-family:"Fira Sans",sans-serif;font-weight:600}
.section{position:absolute;left:0;width:1200px}
.btn{position:absolute;display:flex;align-items:center;justify-content:center;background:var(--green);color:#fff;font-family:"Fira Sans",sans-serif;font-weight:600;font-size:23px;border-radius:4px}
.title{color:var(--green);font-size:37px}
.body-text{font-size:16px;line-height:32px;text-align:justify}

/* top bar */
.topbar{top:0;height:56px;background:#fff}
.topbar .address{left:366px;top:20px;font-size:14px;color:#333}
.lang{top:19px;font-size:14px;color:#333;display:flex;align-items:center;gap:8px}
.flag{width:26px;height:15px;display:inline-block}
.navbar{top:56px;height:49px;background:var(--orange);z-index:2}
.nav{left:367px;top:16px;display:flex;gap:22px;font-size:15px;color:#fff}
.logo-box{left:88px;top:56px;width:262px;height:79px;background:#fff;border-radius:0 0 6px 6px;box-shadow:0 2px 6px rgba(0,0,0,.25);z-index:3;display:flex;align-items:center;gap:12px;padding-left:18px}
.logo-square{width:48px;height:48px;background:var(--lime)}
.logo-name{font-family:"Fira Sans",sans-serif;font-weight:600;font-size:16px;color:var(--green);line-height:20px}

/* hero */
.hero{top:105px;height:536px;background:linear-gradient(100deg,#5b5a4c 0%,#7d7558 45%,#9c8c62 70%,#6c6a55 100%)}
.hero h1{left:90px;top:130px;font-size:53px;color:#fff;font-weight:700}
.hero p{left:90px;top:207px;width:520px;font-size:17px;line-height:28px;color:#fff}
.hero .btn{left:90px;top:291px;width:232px;height:60px}

/* welcome */
.welcome{top:641px;height:540px}
.welcome h2{left:90px;top:90px}
.welcome p{left:90px;top:160px;width:524px}
.welcome .btn{left:90px;top:383px;width:232px;height:60px}
.welcome .photo{left:709px;top:92px;width:401px;height:355px;border-radius:6px;background:linear-gradient(160deg,#9aa0a8,#5d646d 60%,#7a7f86)}

/* expertise */
.expertise{top:1181px;height:533px;background:linear-gradient(100deg,#d9a516 0%,#f0bf26 50%,#f8cd36 100%)}
.expertise h2{width:100%;top:52px;text-align:center;color:#fff;font-size:40px}
.expertise p{left:140px;width:920px;top:118px;text-align:center;color:#fff;font-size:17px;line-height:34px}
.circle{width:168px;height:168px;border-radius:50%;background:#0d0d0d;border:7px solid #fff;box-shadow:0 0 0 4px rgba(0,0,0,.15);display:flex;align-items:center;justify-content:center}
.exp-label{top:420px;width:300px;text-align:center;color:#fff;font-family:"Fira Sans",sans-serif;font-weight:600;font-size:21px}

/* services */
.services{top:1714px;height:508px}
.services h2{left:101px;top:116px}
.services p{left:530px;top:92px;width:582px;font-size:15.5px;line-height:28px}
.tile{top:225px;height:187px;overflow:hidden}
.tile span{position:absolute;left:0;right:0;bottom:0;height:36px;padding:8px 0 0 34px;background:linear-gradient(transparent,rgba(0,0,0,.6));color:#fff;font-family:"Fira Sans",sans-serif;font-weight:600;font-size:17px}

/* partners */
.partners{top:2222px;height:390px;background:var(--gray-bg)}
.partners h2{left:88px;top:90px}
.partners p{left:88px;top:152px;width:436px}
.badges{left:600px;top:133px;width:510px;height:126px;background:#fff;border:1px solid #ddd;display:flex}
.badge-cell{flex:1;border-right:1px solid #ddd;display:flex;align-items:center;justify-content:center}
.badge-cell:last-child{border-right:none}

/* conditions */
.conditions{top:2612px;height:570px}
.conditions .photo{left:88px;top:105px;width:403px;height:362px;border-radius:6px;background:linear-gradient(150deg,#4e5560,#8b8f92 50%,#b34a2a 85%)}
.conditions h2{left:576px;top:100px}
.conditions p{left:576px;top:157px;width:526px}
.cond-item{display:flex;align-items:center;gap:16px;color:var(--lime);font-family:"Fira Sans",sans-serif;font-weight:600;font-size:21px}

/* projects */
.projects{top:3182px;height:568px;background:linear-gradient(90deg,#0e8a3a,#1f9a45 60%,#16903e)}
.projects h2{width:100%;top:40px;text-align:center;color:#fff;font-size:40px}
.projects p{left:180px;width:840px;top:104px;text-align:center;color:#fff;font-size:18px;line-height:32px}
.proj-img{top:197px;width:332px;height:210px;display:flex;align-items:center;justify-content:center}
.proj-cap{top:434px;width:360px;text-align:center;color:#fff;font-family:"Fira Sans",sans-serif;font-weight:600;font-size:15.5px;line-height:22px}
.dots{top:510px;left:572px;display:flex;gap:14px}
.dot{width:14px;height:14px;border-radius:50%;border:2px solid #fff}
.dot.on{background:#fff}

/* team */
.team{top:3750px;height:746px}
.team h2{width:100%;top:98px;text-align:center;color:var(--green);font-size:37px}
.team p{left:140px;width:920px;top:152px;text-align:center;font-size:17px;line-height:32px}
.card{top:300px;width:309px;height:381px;background:#f3f3f3}
.card .pic{height:306px}
.card .cap{text-align:center;padding-top:12px;color:#222;font-size:18px;line-height:26px}
.card .cap b{font-family:"Fira Sans",sans-serif;font-weight:600;font-size:20px}
.card.info{background:linear-gradient(135deg,#f1ebe4,#d9cfc5)}
.card.info .cap{padding-top:102px;line-height:32px;color:#444;font-size:16px}

/* footer */
.footer{top:4496px;height:331px;background:var(--dark);color:#fff}
.foot-logo{left:400px;top:49px;display:flex;align-items:center;gap:16px}
.foot-logo .logo-square{width:90px;height:90px}
.foot-logo .logo-name{color:#fff;font-size:29px;line-height:36px}
.foot-nav{top:192px;width:100%;display:flex;justify-content:center;gap:34px;font-size:17px}
.foot-contact{top:230px;width:100%;display:flex;justify-content:center;align-items:center;gap:12px;font-size:17px}
.foot-copy{top:282px;width:100%;text-align:center;font-size:16px}
</style>
</head>
<body>

<header class="section topbar">
  <div class="abs address">1. Pramenova s.r.o, ID 4719 Lindenweg 14 01067 Görlitz</div>
  <div class="abs lang" style="left:818px"><span class="flag" style="background:#1f3a7a"></span>English</div>
  <div class="abs lang" style="left:923px"><span class="flag" style="background:linear-gradient(#fff 50%,#d7141a 50%)"></span>Czech</div>
  <div class="abs lang" style="left:1014px"><span class="flag" style="background:linear-gradient(#000 33%,#dd0000 33% 66%,#ffce00 66%)"></span>Deutsch</div>
</header>

<nav class="section navbar">
  <div class="abs nav">
    <span>The Enterprise</span><span>Leistunsgen</span><span>Our Projects</span><span>Cooperation Partners</span><span>Calls For Cooperation</span><span>Contact</span>
  </div>
</nav>
<div class="abs logo-box">
  <div class="logo-square"></div>
  <div class="logo-name">1. PRAMENOVA SRO<br>Beratungsfirma</div>
</div>

<section class="section hero" role="img" aria-label="Photo of a team inspecting cut timber in a forest with a tablet">
  <h1 class="abs">1. PRAMENOVA SRO</h1>
  <p class="abs">At present we are working for completed portfolio of clients as supervisors of development and innovative projects.</p>
  <div class="btn">Get Started</div>
</section>

<section class="section welcome">
  <h2 class="abs title">Welcome To Our Company</h2>
  <p class="abs body-text">Our company was founded in 2008 and started to work as a counsilary company operating in the section of European funds administrated by Czech republic. Nowadays we are specialising on projects in the sphere of science and research co-financed by EU.Since 6.6.2013 we are registered under European commission for a purpose of broad support of transnational projects.</p>
  <div class="btn">Read More</div>
  <div class="abs photo" role="img" aria-label="Photo of workers in a wood workshop"></div>
</section>

<section class="section expertise">
  <h2 class="abs">Area of Expertise</h2>
  <p class="abs">Lorem ipsum dolor sit amet, consectetur adipiscing elit. Etiam sem neque, consectetur id varius nec, euismod sit amet mauris. Nunc feugiat libero vitae lectus tincidunt porttitor sed nec ligula.</p>
  <div class="abs circle" style="left:152px;top:235px">
    <svg class="exp-icon" width="84" height="84" viewBox="0 0 84 84" fill="none" stroke="#fff" stroke-width="4" stroke-linecap="round" stroke-linejoin="round" aria-label="Axe icon" role="img">
      <path d="M62 14L30 46"/>
      <path d="M24 36l16 16-8 8c-8 0-16-8-16-16z"/>
      <path d="M14 70h46"/>
    </svg>
  </div>
  <div class="abs circle" style="left:518px;top:235px">
    <svg class="exp-icon" width="84" height="84" viewBox="0 0 84 84" fill="none" stroke="#fff" stroke-width="4" stroke-linecap="round" stroke-linejoin="round" aria-label="Circular saw icon" role="img">
      <circle cx="42" cy="42" r="22"/>
      <circle cx="42" cy="42" r="6"/>
      <path d="M42 14v6M42 64v6M14 42h6M64 42h6M22 22l4 4M58 58l4 4M62 22l-4 4M26 58l-4 4"/>
    </svg>
  </div>
  <div class="abs circle" style="left:878px;top:235px">
    <svg class="exp-icon" width="84" height="84" viewBox="0 0 84 84" fill="none" stroke="#fff" stroke-width="4" stroke-linecap="round" stroke-linejoin="round" aria-label="Drill icon" role="img">
      <rect x="16" y="24" width="38" height="18" rx="3"/>
      <path d="M54 30h10M64 33h10"/>
      <path d="M24 42l-4 24h16l2-24"/>
      <path d="M18 66h22"/>
    </svg>
  </div>
  <div class="abs exp-label" style="left:86px">Neque porro quisquam</div>
  <div class="abs exp-label" style="left:452px">Neque porro quisquam</div>
  <div class="abs exp-label" style="left:812px">Neque porro quisquam</div>
</section>

<section class="section services">
  <h2 class="abs title">Our Services</h2>
  <p class="abs">Lorem ipsum dolor sit amet, consectetur adipiscing elit. Mauris luctus felis vel quam fringilla efficitur. Etiam dictum quam vitae urna.gravida fringilla. Lorem Cras vitae mollis est, et tristique dolor.</p>
  <div class="abs tile" style="left:90px;width:249px;background:linear-gradient(#9db7cf,#8a6a4a)" role="img" aria-label="Timber frame construction site"><span>Project Coordination</span></div>
  <div class="abs tile" style="left:347px;width:247px;background:linear-gradient(135deg,#8a7152,#c9b089)" role="img" aria-label="Glulam timber beams"><span>EU Projects</span></div>
  <div class="abs tile" style="left:602px;width:249px;background:linear-gradient(#f2f2f2,#d9cfc4)" role="img" aria-label="Small wooden houses models"><span>Project Financing</span></div>
  <div class="abs tile" style="left:859px;width:249px;background:linear-gradient(#c6553a,#a2492f)" role="img" aria-label="Stacked timber for export"><span>Export Promotion</span></div>
</section>

<section class="section partners">
  <h2 class="abs title">Our Partners</h2>
  <p class="abs body-text">Lorem ipsum dolor sit amet, consectetur adipiscing elit. Etiam sem neque, consectetur id varius nec, euismod sit amet mauris. Nunc feugiat libero vitae lectus tincidunt porttitor sed nec ligula.</p>
  <div class="abs badges">
    <div class="badge-cell"><svg width="130" height="60"><rect width="130" height="60" rx="4" fill="#c9d6e8"/></svg></div>
    <div class="badge-cell"><svg width="130" height="60"><rect width="130" height="60" rx="4" fill="#e6dde3"/></svg></div>
    <div class="badge-cell"><svg width="130" height="60"><rect width="130" height="60" rx="4" fill="#2a4a8c"/></svg></div>
  </div>
</section>

<section class="section conditions">
  <div class="abs photo" role="img" aria-label="Photo of engineers reviewing a tablet in a workshop"></div>
  <h2 class="abs title">Conditions Of Our Services</h2>
  <p class="abs body-text">Lorem ipsum dolor sit amet, consectetur adipiscing elit. Etiam sem neque, consectetur id varius nec, euismod sit amet mauris. Nunc feugiat libero vitae lectus tincidunt porttitor sed nec ligula. Donec eu urna a lectus sollicitudin tempor at at odio. Nam efficitur molestie orci eu tempus. Cras aliquet scelerisque sapien ac aliquet.</p>
  <div class="abs cond-item" style="left:572px;top:353px"><svg width="34" height="34" viewBox="0 0 34 34"><path d="M6 6L28 28M28 6L6 28" stroke="#666" stroke-width="4" stroke-linecap="round"/></svg>Quisquam</div>
  <div class="abs cond-item" style="left:770px;top:353px"><svg width="34" height="34" viewBox="0 0 34 34"><path d="M6 6L28 28M28 6L6 28" stroke="#666" stroke-width="4" stroke-linecap="round"/></svg>Quisquam</div>
  <div class="abs cond-item" style="left:572px;top:400px"><svg width="34" height="34" viewBox="0 0 34 34"><path d="M6 6L28 28M28 6L6 28" stroke="#666" stroke-width="4" stroke-linecap="round"/></svg>Quisquam</div>
  <div class="abs cond-item" style="left:770px;top:400px"><svg width="34" height="34" viewBox="0 0 34 34"><path d="M6 6L28 28M28 6L6 28" stroke="#666" stroke-width="4" stroke-linecap="round"/></svg>Quisquam</div>
</section>

<section class="section projects">
  <h2 class="abs">Successful Projects</h2>
  <p class="abs">Lorem ipsum dolor sit amet, consectetur adipiscing elit. Etiam sem neque, consectetur id varius nec, euismod sit amet mauris.</p>
  <div class="abs proj-img" style="left:90px;background:linear-gradient(#e6e9ee,#8a8f96)" role="img" aria-label="Video still of a light aircraft in a hangar">
    <svg width="34" height="34"><circle cx="17" cy="17" r="15" fill="#fff" opacity=".85"/><path d="M13 10L24 17L13 24Z" fill="#333"/></svg></div>
  <div class="abs proj-img" style="left:435px;background:linear-gradient(#9aa0a6,#4a4a42)" role="img" aria-label="Video still of a forestry tractor">
    <svg width="34" height="34"><circle cx="17" cy="17" r="15" fill="#fff" opacity=".85"/><path d="M13 10L24 17L13 24Z" fill="#333"/></svg></div>
  <div class="abs proj-img" style="left:782px;background:linear-gradient(#c9ccd0,#e8e2d8)" role="img" aria-label="Video still of a renovated town building">
    <svg width="34" height="34"><circle cx="17" cy="17" r="15" fill="#fff" opacity=".85"/><path d="M13 10L24 17L13 24Z" fill="#333"/></svg></div>
  <div class="abs proj-cap" style="left:76px">Innovation Of The Development Activities<br>Of The Company Aerolinka (2013)</div>
  <div class="abs proj-cap" style="left:421px">The Development Of The Company<br>Horská Lesní Sro (2008-2013)</div>
  <div class="abs proj-cap" style="left:768px">The Development Of The<br>City Of Lipenec (2009-2013)</div>
  <div class="abs dots"><span class="dot"></span><span class="dot on"></span><span class="dot"></span></div>
</section>

<section class="section team">
  <h2 class="abs">Our Team</h2>
  <p class="abs">Lorem ipsum dolor sit amet, consectetur adipiscing elit. Etaiam sem neque, consectetur id varius nec, euismod sit amet mauris. Nunc feugiat libero vitae lectus tincidunt porttitor sed nec ligula.</p>
  <div class="abs card" style="left:90px">
    <div class="pic" style="background:linear-gradient(#7d8a7a,#3f3a36)" role="img" aria-label="Portrait photo of the managing director"></div>
    <div class="cap"><b>Geschäftsführer</b><br>Projekt manager</div>
  </div>
  <div class="abs card" style="left:439px">
    <div class="pic" style="background:linear-gradient(#f4f4f4,#cbb8a8)" role="img" aria-label="Portrait photo of the project manager"></div>
    <div class="cap"><b>Mgr. Lenka Horáková</b><br>Projekt manager</div>
  </div>
  <div class="abs card info" style="left:801px" role="img" aria-label="Faded portrait photo behind contact details">
    <div class="cap"><b>Tomáš Brenek</b><br>Projektberater<br>T: +420 600 987 654<br>Email: brenek@pramenova-example.eu<br>Die Sprache Ihrer Wahl ist English</div>
  </div>
</section>

<footer class="section footer">
  <div class="abs foot-logo">
    <div class="logo-square"></div>
    <div class="logo-name">1. PRAMENOVA SRO<br>Beratungsfirma</div>
  </div>
  <div class="abs foot-nav"><span>The Enterprise</span><span>Leistunsgen</span><span>Our Projects</span><span>Cooperation Partners</span><span>Calls For Cooperation</span><span>Contact</span></div>
  <div class="abs foot-contact">
    <svg width="14" height="20" viewBox="0 0 14 20"><path d="M7 0C3 0 0 3 0 7c0 5 7 13 7 13s7-8 7-13c0-4-3-7-7-7z" fill="#fff"/><circle cx="7" cy="7" r="2.5" fill="#2f2f2f"/></svg>
    <span>1. Pramenova sro, ID 4719 Lindenweg 14 01067 Görlitz</span>
    <svg width="18" height="18" viewBox="0 0 24 24" style="margin-left:14px"><path d="M6.6 10.8a15 15 0 006.6 6.6l2.2-2.2c.3-.3.7-.4 1-.2 1.1.4 2.3.6 3.6.6.6 0 1 .4 1 1V20c0 .6-.4 1-1 1C10.6 21 3 13.4 3 4c0-.6.4-1 1-1h3.5c.6 0 1 .4 1 1 0 1.3.2 2.5.6 3.6.1.3 0 .7-.2 1z" fill="#fff"/></svg>
    <span>+420 600 123 456</span>
    <svg width="18" height="14" viewBox="0 0 18 14" style="margin-left:24px"><rect width="18" height="14" rx="1" fill="#fff"/><path d="M1 1l8 6 8-6" stroke="#2f2f2f" stroke-width="1.5" fill="none"/></svg>
    <span style="margin-left:14px">kontakt@pramenova-example.eu</span>
  </div>
  <div class="abs foot-copy">© 2019 Pramenova. All Rights Reserved</div>
</footer>

</body>
</html>
```